Business cards to launch an education platform

Hi,
I am looking at having new business cards designed.
I am a startup, developing a web platform for schools and university, the education world. It's an online assessment system.
I would like a card that looks classy, and that is using the colors and the font of my logo.

I have attached:
1) my logo
2) A business card that I have designed quickly so you can have all the information required in the card, but I really don't like it.
3) The font that I am using (Lato Regular) to design my web platform
4) Some screenshots of my web platform so you can have a look at the style that I have.

Target Market(s)

Major market: Education system: Schools and university
Minor markets: Business in general

Industry/Entity Type

Business

Contact Information for Business Card

Clara Fenwick
Director

M: 0437 518 902
E: clara.fenwick@amberLoomSystems.com.au

Requirements
Must have
• The colors of my logo

```html
<!DOCTYPE html>
<html lang="en">
<head>
<meta charset="utf-8">
<title>Amber Loom Systems — Business Cards</title>
<link rel="stylesheet" href="https://fonts.googleapis.com/css2?family=Lato:wght@400;700&display=swap">
<style>
  :root {
    --page-bg: #e9eaec;
    --card-white: #f4f4f5;
    --navy: #0b3a6c;
    --navy-deep: #0a3462;
    --brand-blue: #1d5fa8;
    --accent-cyan: #22c4e4;
    --ink: #3f4247;
    --light-text: #e8eef6;
  }
  * { margin: 0; padding: 0; box-sizing: border-box; }
  html, body {
    width: 1105px; height: 1200px; overflow: hidden;
    background: var(--page-bg);
    font-family: "Lato", sans-serif;
  }
  .canvas { position: relative; width: 1105px; height: 1200px; }

  .card {
    position: absolute; left: 182px; width: 747px; height: 427px;
    overflow: hidden;
  }

  /* Front */
  .card--front { top: 119px; background: var(--card-white); }
  .front__band {
    position: absolute; left: 0; top: 58px; width: 430px; height: 117px;
    background: var(--navy);
  }
  .front__name {
    position: absolute; left: 52px; top: 89px;
    font-size: 27px; font-weight: 700; color: #ffffff; letter-spacing: 0.3px;
  }
  .front__role {
    position: absolute; left: 52px; top: 124px;
    font-size: 19px; font-weight: 400; color: #ffffff;
  }
  .front__brand {
    position: absolute; left: 384px; top: 96px;
    display: flex; align-items: center; gap: 14px;
  }
  .brand__square { width: 40px; height: 40px; background: var(--brand-blue); }
  .front__brand-name {
    font-size: 30px; font-weight: 400; color: var(--brand-blue);
    letter-spacing: 1.5px; text-transform: uppercase;
  }
  .front__contact {
    position: absolute; left: 0; right: 0; top: 330px;
    text-align: center; color: var(--ink);
  }
  .front__phone { font-size: 20px; font-weight: 700; line-height: 28px; }
  .front__email { font-size: 20px; font-weight: 400; line-height: 30px; }

  /* Back */
  .card--back {
    top: 637px;
    background: radial-gradient(circle at 82% 55%, #114a86 0%, var(--navy-deep) 55%);
  }
  .back__brand-name {
    position: absolute; left: 52px; top: 40px;
    font-size: 44px; font-weight: 400; color: var(--light-text);
    letter-spacing: 3px; line-height: 1.1; text-transform: uppercase;
  }
  .back__points {
    position: absolute; left: 52px; top: 158px; list-style: none;
  }
  .back__points li {
    position: relative; padding-left: 20px;
    font-size: 20px; line-height: 29px; color: var(--light-text);
  }
  .back__points li::before {
    content: ""; position: absolute; left: 0; top: 12px;
    width: 7px; height: 7px; border-radius: 50%; background: var(--accent-cyan);
  }
  .back__web {
    position: absolute; left: 52px; top: 358px;
    font-size: 20px; color: var(--light-text);
  }
</style>
</head>
<body>
<main class="canvas">
  <section class="card card--front" aria-label="Business card front">
    <div class="front__band"></div>
    <h1 class="front__name">CLARA FENWICK</h1>
    <p class="front__role">DIRECTOR</p>
    <div class="front__brand">
      <span class="brand__square" aria-hidden="true"></span>
      <span class="front__brand-name">Amber Loom Systems</span>
    </div>
    <div class="front__contact">
      <p class="front__phone">0437 518 902</p>
      <p class="front__email">clara.fenwick@amberLoomSystems.com.au</p>
    </div>
  </section>

  <section class="card card--back" aria-label="Business card back">
    <h2 class="back__brand-name">Amber Loom<br>Systems</h2>
    <ul class="back__points">
      <li>Lorem ipsum dolor</li>
      <li>Wisi mandamus</li>
      <li>Vix cu discere</li>
    </ul>
    <p class="back__web">amberLoomSystems.com.au</p>
  </section>
</main>
</body>
</html>
```